Design NEW business card

We would like a business card using the colour deep red wine or dark navy blue textured background (patterned or not, open to suggestions) with a high gloss debossed rose gold/copper RM Roland Mercer Jewellery business name (Provided). I have included images for your review we would like to keep our currently logo and business name on the front but you can change the layout and positioning. For the back of the card we are open to all suggestions/variations.
Business
Use our current RM Roland Mercer Jewellery logo (Provided image)

```html
<!DOCTYPE html>
<html lang="en">
<head>
<meta charset="utf-8">
<title>Roland Mercer Jewellery – Business Card</title>
<link href="https://fonts.googleapis.com/css2?family=Montserrat:wght@300;400;500&display=swap" rel="stylesheet">
<style>
  :root {
    --page-bg: #e6e6e6;
    --wine: #56202a;
    --rose-gold: #c8946f;
    --rose-gold-light: #dcaa86;
    --copper-dark: #9c7252;
    --card-text: #f1e7e4;
  }
  * { margin: 0; padding: 0; box-sizing: border-box; }
  html, body {
    width: 1200px; height: 960px; overflow: hidden;
    background: var(--page-bg);
    font-family: "Montserrat", Arial, sans-serif;
  }
  .sheet { position: relative; width: 1200px; height: 960px; }

  .card {
    position: absolute; width: 600px; height: 343px;
    box-shadow: 0 2px 4px rgba(0,0,0,0.35);
  }
  .card--front { left: 314px; top: 113px; background: var(--wine); }
  .card--back {
    left: 312px; top: 472px;
    background: radial-gradient(ellipse 60% 75% at 50% 45%, var(--rose-gold-light) 0%, #b98b68 55%, var(--copper-dark) 100%);
  }

  /* brand name (front) */
  .brand {
    position: absolute; text-align: right; color: var(--rose-gold);
    font-weight: 400; text-transform: uppercase;
  }
  .card--front .brand { right: 34px; top: 140px; }
  .brand__name { font-size: 17px; letter-spacing: 3.4px; line-height: 1; }
  .brand__line { font-size: 8px; letter-spacing: 7px; margin-top: 9px; line-height: 1; }

  .card--back .brand {
    left: 0; right: 0; top: 206px; text-align: center; color: var(--wine);
  }
  .card--back .brand__name { font-size: 20px; letter-spacing: 4px; }
  .card--back .brand__line { font-size: 9px; letter-spacing: 9px; margin-top: 10px; }

  /* person */
  .person { position: absolute; left: 38px; top: 158px; }
  .person__name { color: var(--rose-gold); font-size: 19px; font-weight: 400; letter-spacing: 0.3px; }
  .person__role { color: var(--card-text); font-size: 13px; margin-top: 6px; letter-spacing: 0.3px; }

  .contacts { position: absolute; left: 38px; top: 217px; list-style: none; }
  .contacts li {
    display: flex; align-items: center; height: 19px;
    color: var(--card-text); font-size: 14px; letter-spacing: 0.3px;
  }
  .contacts svg { width: 14px; height: 14px; margin-right: 10px; fill: var(--rose-gold); flex: none; }

  .divider {
    position: absolute; left: 237px; top: 274px; width: 1px; height: 36px; background: var(--card-text);
  }
  .address {
    position: absolute; left: 262px; top: 274px;
    color: var(--card-text); font-size: 14px; line-height: 19px; letter-spacing: 0.3px; font-style: normal;
  }

  .website {
    position: absolute; left: 0; right: 0; top: 293px; text-align: center;
    color: var(--wine); font-size: 13px; font-weight: 500; letter-spacing: 5px;
  }
</style>
</head>
<body>
<main class="sheet">

  <section class="card card--front">
    <div class="brand">
      <div class="brand__name">Roland Mercer</div>
      <div class="brand__line">Jewellery</div>
    </div>

    <div class="person">
      <div class="person__name">CLAIRE HOLLIS</div>
      <div class="person__role">CEO/FOUNDER</div>
    </div>

    <ul class="contacts">
      <li><svg viewBox="0 0 16 16"><path d="M3.5 1l2.5 3-1.5 2c1 2 3 4 5 5l2-1.5 3 2.5-1.5 2.5C7 14.5 1.5 9 1 2.5z"/></svg>689 512 7403</li>
      <li><svg viewBox="0 0 16 16"><path d="M4 0h8a1 1 0 0 1 1 1v14a1 1 0 0 1-1 1H4a1 1 0 0 1-1-1V1a1 1 0 0 1 1-1zm1 2v10h6V2zm3 11a1 1 0 1 0 0 2 1 1 0 0 0 0-2z"/></svg>836 270 4185</li>
      <li><svg viewBox="0 0 16 16"><path d="M4 1h8v4H4zM1 6h14v7h-2v2H3v-2H1zm4 5v2h6v-2z"/></svg>482 731 6059</li>
      <li><svg viewBox="0 0 16 16"><path d="M1 3h14v1L8 9 1 4zm0 3l7 5 7-5v7H1z"/></svg>hello@rmercer.com</li>
      <li><svg viewBox="0 0 16 16"><circle cx="8" cy="8" r="7"/></svg>www.rmercer.com</li>
    </ul>

    <div class="divider"></div>
    <address class="address">2140 Harbor View Drive<br>Juneau, Alaska 99801</address>
  </section>

  <section class="card card--back">
    <div class="brand">
      <div class="brand__name">Roland Mercer</div>
      <div class="brand__line">Jewellery</div>
    </div>
    <div class="website">www.rmercer.com</div>
  </section>

</main>
</body>
</html>
```